I require my existing website to be updated

I have an existing website on Squarespace. I would like to refresh it, change some of the copy, add in my new video that we created. I want to give it a new look. My branding is all about geese flying in the V formation, and how that plays out in business when we align our people to our purpose. I have used Pick-Pick-Pebble in the previous site, and now want The Rolling Arc @ Office to replace that narrative. The website is colourful, fun, but needs to have a professional look and I am also looking for more audience engagement on the site. I would like to highlight to a professional small to medium size business audience. I would like to highlight my Brookcast, showcase my speaking, and really utilize the metaphor to put me in a category of one in the speaking and consulting world. My present website is www.meridanpathways.ca

Since the website is on Squarespace, does it need to be coded?

To be clear, I already have a site on Squarespace, I do not need a new site. For those interested in the project, can we make the changes to my existing site, instead of creating and hosting a new one????

I have a new video which I will be uploading.
Updates

Here is the link to the video that I need on my website https://qx.example/Tr83mPzd

Target Market(s)

Small to medium size businesses -

Industry/Entity Type

Business Consulting, Coaching, Speaking

Number of Pages Required

5+ page

Font styles to use
Other font styles liked:
• Calibri, Marydale, Futura

Requirements
Must have
• Color, fun, and showcase The Rolling Arc @ Office. It must have my video, Brookcast, and a place for people to want to engage. My case study and e-book to download. Logo's of companies that I have worked with
Nice to have
• A place for people to engage with the site. Testimonials from clients. Copy or video.
Should not have
• A traditional or boring look

```html
<!DOCTYPE html>
<html lang="en">
<head>
<meta charset="UTF-8">
<title>Meridan Pathways</title>
<link href="https://fonts.googleapis.com/css2?family=Carlito:wght@400;700&family=Roboto:wght@400;500;700&display=swap" rel="stylesheet">
<style>
:root{
  --ink:#0b0b0b;
  --white:#ffffff;
  --text:#222222;
  --muted:#555555;
  --panel:#eceef1;
  --tile:#ffffff;
  --sky-top:#5d7fa3;
  --sky-mid:#b7a79a;
  --sky-low:#e0a25a;
  --water:#3f6fa6;
  --shadow:0 4px 14px rgba(0,0,0,.14);
}
*{margin:0;padding:0;box-sizing:border-box}
html,body{width:1200px;height:4111px;overflow:hidden;background:var(--white)}
body{position:relative;font-family:"Roboto",sans-serif;color:var(--text)}
.abs{position:absolute}
h2,.heading{font-family:"Carlito",sans-serif;font-weight:700;color:var(--ink)}

/* header */
.site-header{left:0;top:0;width:1200px;height:123px;background:var(--white)}
.brand{left:100px;top:22px;display:flex;align-items:center;gap:12px}
.brand-dot{width:46px;height:46px;border-radius:50%;background:var(--ink)}
.brand-name{font-family:"Carlito",sans-serif;font-weight:700;font-size:17px;letter-spacing:2px;color:var(--ink);line-height:1.1}
.main-nav{top:47px;left:0;width:1200px;font-family:"Roboto",sans-serif;font-weight:500;font-size:15px;color:var(--ink)}
.main-nav span{position:absolute;white-space:nowrap}
.search-icon{left:1066px;top:45px}

/* hero */
.hero{left:0;top:123px;width:1200px;height:515px;background:linear-gradient(180deg,var(--sky-top) 0%,#8ea0b3 40%,var(--sky-mid) 70%,var(--sky-low) 100%)}
.hero-title{left:112px;top:278px;font-family:"Carlito",sans-serif;font-weight:700;font-size:42px;line-height:62px;color:var(--ink);text-shadow:0 0 6px rgba(255,255,255,.7)}
.torn{left:0;width:1200px}

/* about */
.about-photo{left:99px;top:713px;width:463px;height:447px;border-radius:50%;background:radial-gradient(circle at 40% 40%,#8fb0d6,var(--water) 70%);border:4px solid var(--ink)}
.about-title{left:616px;top:736px;font-size:29px}
.about-copy{left:616px;top:797px;width:480px;font-size:19px;line-height:37px;color:var(--text)}
.learn-btn{left:598px;top:1084px;width:245px;height:60px;background:var(--ink);display:flex;align-items:center}
.learn-btn .dot{width:64px;height:64px;margin-left:-4px;border-radius:50%;background:var(--white);border:6px solid var(--ink)}
.learn-btn span{font-family:"Carlito",sans-serif;font-weight:700;font-size:24px;color:var(--white);margin-left:12px}

.section-title{left:0;width:1200px;text-align:center;font-size:29px}

/* brookcast */
.cast-frame{left:112px;top:1337px;width:463px;height:484px;border:7px solid var(--ink);background:linear-gradient(135deg,#d9c8a8,#b09472 55%,#3f5a55)}
.play{left:490px;top:1742px;width:44px;height:44px;border-radius:50%;background:var(--ink);border:3px solid var(--white)}
.cast-card{left:575px;top:1451px;width:513px;height:241px;background:var(--white);box-shadow:var(--shadow);padding:52px 40px 0 70px;font-size:19px;line-height:37px}

/* case study */
.case-card{top:1981px;width:286px;height:330px;background:var(--white);border-radius:8px;box-shadow:var(--shadow);overflow:hidden}
.case-img{width:286px;height:222px}
.case-icon{position:absolute;left:108px;top:193px;width:70px;height:70px;border-radius:50%;background:var(--ink);border:4px solid var(--white)}
.case-label{position:absolute;top:278px;width:100%;text-align:center;font-family:"Carlito",sans-serif;font-weight:700;font-size:20px;color:var(--ink)}

/* ebook */
.ebook-band{left:0;top:2399px;width:1200px;height:212px;background:var(--ink)}
.ebook-title{left:228px;top:2432px;width:300px;text-align:center;font-family:"Carlito",sans-serif;font-weight:700;font-size:30px;color:var(--white)}
.download{left:243px;top:2496px;width:284px;height:64px}
.download span{position:absolute;left:65px;top:20px;font-family:"Roboto",sans-serif;font-weight:500;font-size:20px;color:var(--ink)}
.books{left:731px;top:2370px;width:271px;height:263px;border-radius:10px;background:linear-gradient(160deg,#6f9a3c 0%,#3f6a86 50%,#8a4d25 100%)}

/* clients */
.clients{left:110px;top:2694px;width:980px;height:493px;background:var(--panel);box-shadow:var(--shadow)}
.client-tile{width:151px;height:126px;background:var(--tile);display:flex;align-items:center;justify-content:center;gap:6px;text-align:center;padding:6px;font-family:"Roboto",sans-serif;font-weight:700;font-size:15px;color:#333}
.client-tile i{display:block;width:14px;height:14px;border-radius:50%;background:#333;flex:none}

/* testimonials */
.quote-card{top:3350px;width:317px;height:308px;background:var(--white);box-shadow:var(--shadow);overflow:hidden}
.quote-mark{position:absolute;left:10px;top:8px;font-family:"Carlito",sans-serif;font-weight:700;font-size:28px;color:var(--ink)}
.quote-text{position:absolute;top:38px;left:20px;width:277px;text-align:center;font-size:19px;line-height:37px;color:var(--text)}
.quote-wave{position:absolute;left:0;bottom:0}
.avatar{position:absolute;left:115px;top:150px;width:86px;height:86px;border-radius:50%;border:3px solid var(--white)}
.quote-name{position:absolute;top:262px;width:100%;text-align:center;font-family:"Carlito",sans-serif;font-weight:700;font-size:22px;color:var(--white)}

/* footer */
.footer{left:0;top:3740px;width:1200px;height:371px;background:var(--ink)}
.footer-mark{left:533px;top:3790px;width:134px;height:134px;border-radius:50%;background:var(--white)}
.footer-name{left:0;width:1200px;top:3935px;text-align:center;font-family:"Carlito",sans-serif;font-weight:700;font-size:19px;letter-spacing:4px;color:var(--white)}
.social{left:0;width:1200px;top:3994px;text-align:center;font-family:"Roboto",sans-serif;font-weight:700;font-size:17px;color:var(--white)}
.social span{margin:0 12px}
.footer-rule{left:112px;top:4051px;width:976px;height:1px;background:#555}
.copyright{left:0;width:1200px;top:4073px;text-align:center;font-family:"Roboto",sans-serif;font-weight:700;font-size:15px;color:var(--white)}
</style>
</head>
<body>

<header class="site-header abs">
  <div class="brand abs"><div class="brand-dot"></div><div class="brand-name">MERIDAN<br>PATHWAYS</div></div>
  <nav class="main-nav abs">
    <span style="left:423px">HOME</span>
    <span style="left:520px">BROOKCAST</span>
    <span style="left:651px">TESTIMONIALS</span>
    <span style="left:811px">E BOOK</span>
    <span style="left:917px">CASE STUDY</span>
  </nav>
  <svg class="search-icon abs" width="24" height="24" viewBox="0 0 24 24" fill="none" stroke="#0b0b0b" stroke-width="2"><circle cx="10" cy="10" r="7"/><line x1="15" y1="15" x2="21" y2="21"/></svg>
</header>

<section class="hero abs" role="img" aria-label="Sunset sky with a flock of geese flying in a V formation"></section>
<svg class="torn abs" style="top:618px" width="1200" height="24" viewBox="0 0 1200 24" preserveAspectRatio="none"><path fill="#fff" d="M0 10 L40 4 L80 12 L120 6 L160 14 L200 5 L240 11 L280 3 L320 13 L360 6 L400 12 L440 4 L480 10 L520 5 L560 14 L600 6 L640 11 L680 3 L720 12 L760 6 L800 13 L840 4 L880 11 L920 6 L960 14 L1000 5 L1040 12 L1080 4 L1120 10 L1160 6 L1200 12 L1200 24 L0 24Z"/></svg>
<h1 class="hero-title abs">WELCOME TO<br>MERIDAN PATHWAYS</h1>

<section>
  <div class="about-photo abs" role="img" aria-label="Canada goose skimming over blue water inside a round frame"></div>
  <h2 class="about-title abs">ABOUT US</h2>
  <p class="about-copy abs">Sometimes known as the "Talvo Guy", Dale has quickly become recognized for being the "Pick, Pick, Pebble Guy." An award-winning pioneer in the field of human resources, Dale studies the implications of counter-intuitive work environments on individuals and organizations as a whole. Dale brings insights to employees, employers, and</p>
  <div class="learn-btn abs"><div class="dot"></div><span>LEARN MORE</span></div>
</section>

<section>
  <h2 class="section-title abs" style="top:1247px">BROOKCAST</h2>
  <div class="cast-frame abs" role="img" aria-label="Portrait video still of the speaker in a patterned shirt"></div>
  <svg class="play abs" viewBox="0 0 44 44"><polygon points="17,13 31,22 17,31" fill="#fff"/></svg>
  <div class="cast-card abs">Watch Dale Corwin in action as he walks you through the benefits of Talvo and how it can completely restructure your workplace dynamics.</div>
</section>

<section>
  <h2 class="section-title abs" style="top:1903px">CASE STUDY</h2>
  <div class="case-card abs" style="left:140px"><div class="case-img" role="img" aria-label="Person reviewing charts on a tablet" style="background:linear-gradient(135deg,#cfd6de,#5e6a78)"></div><div class="case-icon"></div><div class="case-label">INDIVIDUALS</div></div>
  <div class="case-card abs" style="left:458px"><div class="case-img" role="img" aria-label="Team discussing around a table" style="background:linear-gradient(135deg,#d8cdbf,#6c5a4b)"></div><div class="case-icon"></div><div class="case-label">TEAMS</div></div>
  <div class="case-card abs" style="left:776px"><div class="case-img" role="img" aria-label="Colleagues joining hands over a meeting table" style="background:linear-gradient(135deg,#e0e2e6,#6a7280)"></div><div class="case-icon"></div><div class="case-label">ORGANIZATIONS</div></div>
</section>

<section>
  <div class="ebook-band abs"></div>
  <div class="ebook-title abs">E BOOK</div>
  <div class="download abs">
    <svg width="284" height="64" viewBox="0 0 284 64"><path d="M0 0 H270 Q284 0 278 14 L264 64 H0 Q22 32 0 0Z" fill="#fff"/><g fill="none" stroke="#0b0b0b" stroke-width="2.5"><line x1="229" y1="18" x2="229" y2="40"/><polyline points="221,32 229,40 237,32"/><polyline points="214,38 214,46 244,46 244,38"/></g></svg>
    <span>DOWNLOAD</span>
  </div>
  <div class="books abs" role="img" aria-label="Stack of hardcover books"></div>
</section>

<section>
  <div class="clients abs"></div>
  <h2 class="section-title abs" style="top:2726px">OUR CLIENTS</h2>
  <div class="client-tile abs" style="left:153px;top:2804px"><i></i>Northvale Soft</div>
  <div class="client-tile abs" style="left:337px;top:2804px">Prairie Response</div>
  <div class="client-tile abs" style="left:520px;top:2804px"><i></i>Ledgerline Records</div>
  <div class="client-tile abs" style="left:704px;top:2804px">Harvest Protein Group</div>
  <div class="client-tile abs" style="left:889px;top:2804px">kvt systems</div>
  <div class="client-tile abs" style="left:153px;top:2968px">Tumble West</div>
  <div class="client-tile abs" style="left:337px;top:2968px">Glance Studio</div>
  <div class="client-tile abs" style="left:520px;top:2968px">clearform</div>
  <div class="client-tile abs" style="left:704px;top:2968px"><i></i>Marlowe</div>
  <div class="client-tile abs" style="left:889px;top:2968px">Province Office</div>
  <svg class="abs" style="left:562px;top:3138px" width="68" height="22" viewBox="0 0 68 22" fill="none" stroke="#0b0b0b" stroke-width="3"><polyline points="12,4 5,11 12,18"/><polyline points="56,4 63,11 56,18"/></svg>
</section>

<section>
  <h2 class="section-title abs" style="top:3268px">TESTIMONIALS</h2>
  <div class="quote-card abs" style="left:104px">
    <div class="quote-mark">&ldquo;</div>
    <p class="quote-text">Cedar Ridge Storage Co.<br>I was first introduced to<br>Dale Corwin and Meridan</p>
    <svg class="quote-wave" width="317" height="150" viewBox="0 0 317 150"><path d="M0 30 Q80 0 158 60 Q240 120 317 40 V150 H0Z" fill="#0b0b0b"/></svg>
    <div class="avatar" role="img" aria-label="Client portrait" style="background:linear-gradient(#c9b8a6,#6d5443)"></div>
    <div class="quote-name">LOREM IPSUM</div>
  </div>
  <div class="quote-card abs" style="left:439px">
    <div class="quote-mark">&ldquo;</div>
    <p class="quote-text">Dale Corwin was a<br>featured speaker at an<br>event I attended recently.</p>
    <svg class="quote-wave" width="317" height="150" viewBox="0 0 317 150"><path d="M0 30 Q80 0 158 60 Q240 120 317 40 V150 H0Z" fill="#0b0b0b"/></svg>
    <div class="avatar" role="img" aria-label="Client portrait" style="background:linear-gradient(#f2a24a,#c0642a)"></div>
    <div class="quote-name">LOREM IPSUM</div>
  </div>
  <div class="quote-card abs" style="left:777px">
    <div class="quote-mark">&ldquo;</div>
    <p class="quote-text">One of the best team<br>building workshops that I<br>have participated in.</p>
    <svg class="quote-wave" width="317" height="150" viewBox="0 0 317 150"><path d="M0 30 Q80 0 158 60 Q240 120 317 40 V150 H0Z" fill="#0b0b0b"/></svg>
    <div class="avatar" role="img" aria-label="Client portrait" style="background:linear-gradient(#e2c79a,#7a5a36)"></div>
    <div class="quote-name">LOREM IPSUM</div>
  </div>
</section>

<footer>
  <svg class="torn abs" style="top:3722px" width="1200" height="24" viewBox="0 0 1200 24" preserveAspectRatio="none"><path fill="#0b0b0b" d="M0 14 L40 6 L80 16 L120 8 L160 18 L200 7 L240 15 L280 5 L320 17 L360 8 L400 15 L440 6 L480 14 L520 7 L560 18 L600 8 L640 15 L680 5 L720 16 L760 8 L800 17 L840 6 L880 15 L920 8 L960 18 L1000 7 L1040 16 L1080 6 L1120 14 L1160 8 L1200 15 L1200 24 L0 24Z"/></svg>
  <div class="footer abs"></div>
  <div class="footer-mark abs"></div>
  <div class="footer-name abs">MERIDAN PATHWAYS</div>
  <div class="social abs"><span>Flitter</span><span>ProLink</span></div>
  <div class="footer-rule abs"></div>
  <div class="copyright abs">@2023 COPYRIGHTS. MERIDAN PATHWAYS. ALL RIGHTS RESERVED.</div>
</footer>

</body>
</html>
```